Marlow Dermal Studio - Business Banner with Brand Elements

Design:
• We would like to get a creative design for a wide banner that will go outside our medical spa clinic location. We need a designer to make a simple yet colorful and high-quality design layout. We want this banner to be eye-catching and to communicate the services we offer at our business: Laser Hair Removal | Veluxin | Lip Filler.

Requirements:
• We would like the banner to include our companies information which is the following:

Logo
“Refresh Your Skin”
Laser Hair Removal | Veluxin | Lip Filler
(520) 867-2291
www.MarlowDermalStudio.com

Colors:
• Our business colors are orange, a hint of black and white, but mostly peach/orange tones. (Orange: #f78f20 , White: #ffffff)

Fonts:
• Josefins Sans Bold & Lato

Content and images can be located here:
https://files.quibbleshare.com/share/folders/7tKwP3zRa9_LmQxVb2nD5yHc04EeJuFs8?mode=viewing

The following will give you an idea of our brand presentation:
• Our website is: www.MarlowDermalStudio.com
• Our Pictavo; @marlowdermalstudio
• Our Lumora: www.lumoranet.com/marlowdermalstudio

Target Market(s)
• Women 25 - 45

Industry/Entity Type
• Beauty

```html
<!DOCTYPE html>
<html lang="en">
<head>
<meta charset="utf-8">
<title>Marlow Dermal Studio – Banner Layouts</title>
<link href="https://fonts.googleapis.com/css2?family=Josefin+Sans:wght@600;700&family=Lato:wght@400;700;900&display=swap" rel="stylesheet">
<style>
  :root{
    --orange:#f78f20;
    --orange-deep:#e8780f;
    --white:#ffffff;
    --ink:#1b1b1b;
    --board:#3a3a3a;
    --board-dark:#2f2f2f;
    --beige:#d9c3a6;
    --beige-light:#e8d9c4;
  }
  *{margin:0;padding:0;box-sizing:border-box}
  html,body{width:1200px;height:2591px;overflow:hidden}
  body{
    position:relative;
    background:radial-gradient(ellipse at 50% 40%, var(--board) 0%, var(--board-dark) 100%);
    font-family:"Lato",sans-serif;
  }
  .sample-label{
    position:absolute;left:65px;
    transform:translate(-50%,-50%) rotate(-90deg);
    color:var(--white);font:700 27px "Lato",sans-serif;white-space:nowrap;
  }
  .banner{
    position:absolute;left:116px;width:968px;height:369px;
    overflow:hidden;background:var(--white);
    box-shadow:0 4px 12px rgba(0,0,0,.35);
  }
  .photo{position:absolute;top:0;bottom:0}
  .shapes{position:absolute;inset:0;width:100%;height:100%}

  .logo{position:absolute;display:flex;align-items:center;gap:12px}
  .logo-dot{width:60px;height:60px;border-radius:50%;background:var(--orange);flex:none}
  .logo-name{font:700 29px "Josefin Sans",sans-serif;color:var(--ink);white-space:nowrap;padding-top:5px}

  .headline{
    position:absolute;font:700 50px/1 "Josefin Sans",sans-serif;
    color:var(--orange);letter-spacing:1px;white-space:nowrap;
  }
  .services{
    position:absolute;height:33px;background:var(--orange);
    display:flex;align-items:center;justify-content:center;
    font:700 21px "Josefin Sans",sans-serif;color:var(--ink);
    letter-spacing:.6px;white-space:nowrap;padding-top:4px;
  }
  .contact-row{
    position:absolute;left:37px;display:flex;align-items:center;gap:12px;
    font:700 27px/1 "Lato",sans-serif;color:var(--ink);white-space:nowrap;
  }
  .icon{width:28px;height:28px;flex:none}
  .icon-pair{position:absolute;display:flex;gap:8px;justify-content:center}
  .centered-line{position:absolute;text-align:center;font:700 27px/1 "Lato",sans-serif;color:var(--ink);white-space:nowrap}
</style>
</head>
<body>

<svg width="0" height="0" style="position:absolute" aria-hidden="true">
  <symbol id="ico-phone" viewBox="0 0 28 28">
    <circle cx="14" cy="14" r="14" fill="currentColor"/>
    <path d="M10.2 7.5c.6-.3 1.2-.1 1.5.5l1.1 2.3c.3.6.1 1.2-.4 1.6l-.9.6c.6 1.6 1.8 2.9 3.3 3.7l.7-.8c.4-.5 1.100-.6 1.6-.3l2.2 1.2c.6.3.8 1 .5 1.5l-.7 1.3c-.4.7-1.2 1.1-2 1-4.6-.6-8.3-4.4-8.8-9-.1-.8.3-1.6 1-2z" fill="var(--glyph,#fff)"/>
  </symbol>
  <symbol id="ico-globe" viewBox="0 0 28 28">
    <circle cx="14" cy="14" r="14" fill="currentColor"/>
    <g fill="none" stroke="var(--glyph,#fff)" stroke-width="1.4">
      <circle cx="14" cy="14" r="7.5"/>
      <ellipse cx="14" cy="14" rx="3.4" ry="7.5"/>
      <path d="M6.5 14h15M7.6 10.2h12.8M7.6 17.8h12.8"/>
    </g>
  </symbol>
</svg>

<!-- Layout 1 -->
<div class="sample-label" style="top:273px">Sample 1</div>
<section class="banner" style="top:89px">
  <div class="photo" role="img" aria-label="Woman in a striped bikini on a sunny beach, hair blowing in the wind"
       style="left:380px;right:0;background:linear-gradient(90deg,#fff 0%,rgba(255,255,255,0) 40%),linear-gradient(180deg,#7fd3d6 0%,#bfe5e3 40%,#d9e8e4 60%,#eee4d6 100%)"></div>
  <div class="logo" style="left:36px;top:28px"><span class="logo-dot"></span><span class="logo-name">Marlow Dermal Studio</span></div>
  <h1 class="headline" style="left:37px;top:143px">REFRESH YOUR SKIN</h1>
  <p class="services" style="left:38px;top:199px;width:552px">LASER HAIR REMOVAL | VELUXIN | LIP FILLER</p>
  <p class="contact-row" style="top:271px"><svg class="icon" style="color:var(--orange)"><use href="#ico-phone"/></svg>(520) 867-2291</p>
  <p class="contact-row" style="top:305px"><svg class="icon" style="color:var(--orange)"><use href="#ico-globe"/></svg>www.MarlowDermalStudio.com</p>
</section>

<!-- Layout 2 -->
<div class="sample-label" style="top:672px">Sample 2</div>
<section class="banner" style="top:488px">
  <div class="photo" role="img" aria-label="Smiling woman in a straw sun hat on a beach"
       style="left:0;width:560px;background:linear-gradient(270deg,#fff 0%,rgba(255,255,255,0) 35%),linear-gradient(180deg,#9fd8dc 0%,#cde9e8 45%,#e9e3d8 100%)"></div>
  <div class="logo" style="left:383px;width:555px;top:24px;justify-content:center"><span class="logo-dot"></span><span class="logo-name">Marlow Dermal Studio</span></div>
  <h1 class="headline" style="left:383px;width:555px;text-align:center;top:134px">REFRESH YOUR SKIN</h1>
  <p class="services" style="left:383px;top:191px;width:552px">LASER HAIR REMOVAL | VELUXIN | LIP FILLER</p>
  <div class="icon-pair" style="left:383px;width:555px;top:241px">
    <svg class="icon" style="color:var(--orange)"><use href="#ico-phone"/></svg>
    <svg class="icon" style="color:var(--orange)"><use href="#ico-globe"/></svg>
  </div>
  <p class="centered-line" style="left:383px;width:555px;top:279px">(520) 867-2291</p>
  <p class="centered-line" style="left:383px;width:555px;top:313px">www.MarlowDermalStudio.com</p>
</section>

<!-- Layout 3 -->
<div class="sample-label" style="top:1075px">Sample 3</div>
<section class="banner" style="top:891px">
  <svg class="shapes" viewBox="0 0 968 369" aria-hidden="true">
    <path d="M250 0 C330 30 400 64 470 60 C560 55 650 22 770 0 Z" fill="var(--orange)"/>
    <path d="M0 369 V272 C90 246 240 244 390 280 C500 308 590 345 650 369 Z" fill="var(--orange)"/>
    <circle cx="860" cy="200" r="248" fill="var(--orange)" opacity=".85"/>
    <circle cx="935" cy="205" r="205" fill="#f2f2f2"/>
  </svg>
  <div class="photo" role="img" aria-label="Smiling woman on a beach, tinted in orange duotone, inside a circle"
       style="left:768px;top:15px;bottom:auto;width:400px;height:400px;border-radius:50%;background:linear-gradient(180deg,#e9a24a 0%,#d88a2e 55%,#c9802c 100%)"></div>
  <div class="logo" style="left:36px;top:28px"><span class="logo-dot"></span><span class="logo-name">Marlow Dermal Studio</span></div>
  <h1 class="headline" style="left:37px;top:143px;color:var(--ink)">REFRESH YOUR SKIN</h1>
  <p class="services" style="left:38px;top:200px;width:552px">LASER HAIR REMOVAL | VELUXIN | LIP FILLER</p>
  <p class="contact-row" style="top:282px;color:var(--white);--glyph:var(--orange)"><svg class="icon" style="color:var(--white)"><use href="#ico-phone"/></svg>(520) 867-2291</p>
  <p class="contact-row" style="top:316px;color:var(--white);--glyph:var(--orange)"><svg class="icon" style="color:var(--white)"><use href="#ico-globe"/></svg>www.MarlowDermalStudio.com</p>
</section>

<!-- Layout 4 -->
<div class="sample-label" style="top:1468px">Sample 4</div>
<section class="banner" style="top:1284px;background:linear-gradient(180deg,var(--beige-light),var(--beige))">
  <svg class="shapes" viewBox="0 0 968 369" aria-hidden="true">
    <path d="M0 0 H560 C480 40 400 70 300 55 C200 40 100 10 0 30 Z" fill="#eadfcd" opacity=".8"/>
  </svg>
  <div class="photo" role="img" aria-label="Three women of different skin tones posing cheek to cheek"
       style="left:470px;right:0;background:linear-gradient(90deg,rgba(217,195,166,1) 0%,rgba(217,195,166,0) 25%),linear-gradient(180deg,#e4d3bd 0%,#caa784 55%,#e9e1d6 100%)"></div>
  <div class="logo" style="left:36px;top:28px"><span class="logo-dot"></span><span class="logo-name">Marlow Dermal Studio</span></div>
  <h1 class="headline" style="left:37px;top:152px;font-size:40px;color:var(--white)">REFRESH YOUR SKIN</h1>
  <p class="services" style="left:38px;top:196px;width:449px;height:28px;font-size:18px">LASER HAIR REMOVAL | VELUXIN | LIP FILLER</p>
  <p class="contact-row" style="top:282px;--glyph:var(--white)"><svg class="icon" style="color:var(--ink)"><use href="#ico-phone"/></svg>(520) 867-2291</p>
  <p class="contact-row" style="top:316px;--glyph:var(--white)"><svg class="icon" style="color:var(--ink)"><use href="#ico-globe"/></svg>www.MarlowDermalStudio.com</p>
</section>

<!-- Layout 5 -->
<div class="sample-label" style="top:1873px">Sample 5</div>
<section class="banner" style="top:1689px">
  <div class="photo" role="img" aria-label="Smiling woman lying on the sand at the water's edge of a tropical beach"
       style="left:300px;right:0;background:linear-gradient(90deg,#fff 0%,rgba(255,255,255,0) 45%),linear-gradient(180deg,#b9dcec 0%,#5fc6d4 22%,#7fd4d6 45%,#eae2d4 70%,#f1ebe2 100%)"></div>
  <div class="logo" style="left:36px;top:28px"><span class="logo-dot"></span><span class="logo-name">Marlow Dermal Studio</span></div>
  <h1 class="headline" style="left:37px;top:143px">REFRESH YOUR SKIN</h1>
  <p class="services" style="left:38px;top:199px;width:552px">LASER HAIR REMOVAL | VELUXIN | LIP FILLER</p>
  <p class="contact-row" style="top:270px"><svg class="icon" style="color:var(--orange)"><use href="#ico-phone"/></svg>(520) 867-2291</p>
  <p class="contact-row" style="top:304px"><svg class="icon" style="color:var(--orange)"><use href="#ico-globe"/></svg>www.MarlowDermalStudio.com</p>
</section>

<!-- Layout 6 -->
<div class="sample-label" style="top:2285px">Sample 6</div>
<section class="banner" style="top:2100px">
  <div class="photo" role="img" aria-label="Laughing woman in a straw hat against a blue sky and sea"
       style="left:480px;right:0;background:linear-gradient(180deg,#6ec6e0 0%,#8fd3e6 40%,#5fc0c9 62%,#dfe9e8 100%)"></div>
  <svg class="shapes" viewBox="0 0 968 369" aria-hidden="true">
    <path d="M524 0 A318 318 0 0 1 524 369" fill="none" stroke="var(--orange)" stroke-width="5"/>
    <path d="M502 0 A300 300 0 0 1 502 369" fill="none" stroke="var(--orange-deep)" stroke-width="8"/>
    <path d="M0 0 H479 A282 282 0 0 1 479 369 H0 Z" fill="var(--orange)"/>
    <circle cx="265" cy="184" r="266" fill="none" stroke="#fbd3a6" stroke-width="3" stroke-dasharray="0.5 9" stroke-linecap="round"/>
  </svg>
  <div class="logo" style="left:37px;width:445px;top:28px;justify-content:center"><span class="logo-dot" style="background:var(--white)"></span><span class="logo-name">Marlow Dermal Studio</span></div>
  <h1 class="headline" style="left:37px;width:445px;text-align:center;top:148px;font-size:40px;color:var(--white)">REFRESH YOUR SKIN</h1>
  <p class="services" style="left:37px;top:193px;width:445px;height:26px;font-size:17.5px;background:var(--ink);color:var(--white)">LASER HAIR REMOVAL | VELUXIN | LIP FILLER</p>
  <div class="icon-pair" style="left:37px;width:445px;top:236px;--glyph:var(--orange)">
    <svg class="icon" style="color:var(--white)"><use href="#ico-phone"/></svg>
    <svg class="icon" style="color:var(--white)"><use href="#ico-globe"/></svg>
  </div>
  <p class="centered-line" style="left:37px;width:445px;top:280px;font-weight:400;color:var(--white)">(520) 867-2291</p>
  <p class="centered-line" style="left:37px;width:445px;top:314px;font-weight:400;color:var(--white)">www.MarlowDermalStudio.com</p>
</section>

</body>
</html>
```